Family business needs stationery redesign with new logo

Family owned company, established in 1987 wanting a brand 'refresh'. We are an electrical, refrigeration and construction company based in the Barkly Region Northern Territory, Australia. We have a new logo we would like to use which is uploaded along with our current letterhead and email signature. We are also dropping the word 'contractors' so please do not include this on any designs. Please note also, the 'orange' color used in our logo and designs should be Northern Territory red ochre which is as follows:

RGB (Hex): #C75B12
PantoneĀ® 159 C
CMYK: 1 / 74 / 100 / 7

We are needing our stationery redesigned using our new logo. Please include letterheads, business cards, envelopes, and email signatures.

We currently use our business letterheads for quotations, invoices, letters, HR matters, and internal memos.

We also need a separate simplified letterhead for internal paperwork such as employee leave forms, meeting agendas, and meeting minutes etc.

Reason: Needing more submissions of full package designs. We are wanting all our stationery, including business cards, letterheads, email signatures, envelopes, etc to be cohesive. We also require ALL the information, as supplied on our template letterhead, to be included on the new letterhead designs. including electrical license no.etc Thank you, R&W

Reason: needing more time as work has got in the way of looking over designs. A lot of designs not meeting the brief/criteria.

Industry/Entity Type

Business

Colors
0355a3
f37122

Requirements
Must have
• The 'orange' color used in the designs should be Northern Territory red ochre which is as follows:
• RGB (Hex): #C75B12
• PantoneĀ® 159 C
• CMYK: 1 / 74 / 100 / 7
• ***MUST INCLUDE ALL INFORMATION THAT IS ON OUR CURRENT LETTERHEAD***
Should not have
• Please do not include the word 'contractors'

```html
<!DOCTYPE html>
<html lang="en">
<head>
<meta charset="utf-8">
<title>R&amp;W Stationery Set</title>
<link href="https://fonts.googleapis.com/css2?family=Arimo:wght@400;700&family=Tinos&family=Open+Sans:wght@400;700&display=swap" rel="stylesheet">
<style>
:root{
  --navy:#1b2f6e;
  --ochre:#c75b12;
  --paper:#ffffff;
  --stage:#e8e9eb;
  --ink:#3a3a3a;
  --muted:#666;
}
*{margin:0;padding:0;box-sizing:border-box}
html,body{width:1200px;height:938px;overflow:hidden;background:var(--stage)}
body{position:relative;font-family:"Arimo",Arial,sans-serif;color:var(--ink)}
.sheet{position:absolute;background:var(--paper);overflow:hidden}
.footer-band{position:absolute;left:0;right:0;bottom:0;background:var(--navy);border-top:1.5px solid var(--ochre);
  color:#fff;font-family:"Open Sans",Arial,sans-serif;display:flex;align-items:center;justify-content:center;letter-spacing:.35em}
.footer-band b{font-weight:700}
.brand-name{font-family:"Arimo",Arial,sans-serif;font-weight:700;color:var(--navy);line-height:1}
.services{font-family:"Tinos","Times New Roman",serif;color:var(--navy)}
/* letterhead */
.letterhead{left:184px;top:67px;width:387px;height:545px}
.letterhead .brand-name{position:absolute;left:20px;top:31px;font-size:25px}
.letterhead .services{position:absolute;left:105px;top:29px;font-size:8.5px;line-height:10px}
.letterhead .contact{position:absolute;right:19px;top:26px;text-align:right;font-size:5.3px;line-height:8.6px;color:var(--muted)}
.letter{position:absolute;left:38px;top:139px;width:295px;font-size:5.3px;line-height:8.4px;color:var(--ink)}
.letter p{margin-bottom:7px}
.letter .date{margin-bottom:6px}
.letter .para-first{margin-bottom:18px}
.letter .para-short{margin-bottom:23px}
.letter .para-last{margin-bottom:10px}
.letter .regards{margin-bottom:8px}
.signature{width:38px;height:26px;background:linear-gradient(90deg,#e8e8e8,#f6f6f6);margin:0 0 9px}
.letter .signer{margin-bottom:4px}
.letterhead .footer-band{height:22px;font-size:8.5px}
/* folder */
.folder{left:637px;top:41px;width:457px;height:575px}
.folder .brand-name{position:absolute;left:0;right:0;top:233px;text-align:center;font-size:46px}
.folder .services{position:absolute;left:0;right:0;top:300px;text-align:center;font-size:16px;line-height:18.5px}
.folder .footer-band{height:24px;font-size:9px}
/* business cards */
.card-front{left:46px;top:660px;width:176px;height:98px}
.card-front .brand-name{position:absolute;left:7px;top:13px;font-size:15px}
.card-front .services{position:absolute;left:64px;top:12px;font-size:5px;line-height:6px}
.card-front .contact{position:absolute;left:7px;top:68px;font-size:3.8px;line-height:5.4px;color:var(--muted)}
.card-front .holder{position:absolute;right:7px;top:70px;text-align:right;font-size:6.2px;line-height:7px}
.card-front .holder b{color:var(--ink)}
.card-front .holder span{color:var(--muted)}
.card-front .footer-band{height:9px;font-size:4.5px}
.card-back{left:46px;top:786px;width:176px;height:99px;background:var(--navy);display:flex;align-items:center;justify-content:center}
.card-back .brand-name{color:#fff;font-size:17px}
/* envelope front */
.envelope{left:266px;top:674px;width:431px;height:207px}
.envelope .brand-name{position:absolute;left:17px;top:27px;font-size:25px}
.envelope .services{position:absolute;left:100px;top:23px;font-size:8.5px;line-height:10px}
.envelope .footer-band{height:25px;font-size:9px}
/* envelope back */
.envelope-back{left:737px;top:672px;width:432px;height:208px}
.envelope-back .flap{position:absolute;left:0;top:0;width:100%;height:72px;background:var(--navy);border-radius:0 0 40px 40px;
  color:#fff;font-family:"Open Sans",Arial,sans-serif;font-size:9px;letter-spacing:.35em;text-align:center;padding-top:30px}
.icon{display:inline-block;vertical-align:middle;margin-left:2px}
</style>
</head>
<body>

<section class="sheet letterhead">
  <div class="brand-name">R&amp;W</div>
  <div class="services">Electrical<br>Refrigeration<br>Building Services</div>
  <div class="contact">
    27 Ochre Street<br>Tennant Creek NT 0860<br>
    555.010.4471 <svg class="icon" width="5" height="5" viewBox="0 0 10 10"><path d="M2 1l2 2-1 1.5c.8 1.5 1.8 2.5 3.3 3.3L7.8 6.8l2 2-1.3 1.2C4.5 9.7.3 5.5 0 1.5L2 1z" fill="#555"/></svg><br>
    office@rwbuild.net <svg class="icon" width="5" height="4" viewBox="0 0 10 8"><rect width="10" height="8" fill="#555"/><path d="M0 0l5 4 5-4" stroke="#fff" fill="none"/></svg>
  </div>
  <div class="letter">
    <p class="date">July 2, 2012</p>
    <p><b>Dear CH,</b><br>ABC Building, def St., Country Name</p>
    <p class="para-first">is simply dummy text of the printing and typesetting industry. Lorem Ipsum has been the industry's standard dummy text ever since the 1500s, when an unknown printer took a galley of type and scrambled it to make a type specimen book. It has survived not only five centuries, but also the leap into electronic typesetting, remaining essentially unchanged. It was popularised in the 1960s with the release of Kernwell sheets containing Lorem Ipsum passages, and more recently with desktop publishing software like Folio Layout including versions of Lorem Ipsum.</p>
    <p class="para-short">is simply dummy text of the printing and typesetting industry. Lorem Ipsum has been the industry's standard dummy text ever since the 1500s, when an unknown printer took a galley of type and scrambled it to make</p>
    <p class="para-last">is simply dummy text of the printing and typesetting industry. Lorem Ipsum has been the industry's standard dummy text ever since the 1500s, when an unknown printer took a galley of type and scrambled it to make a type specimen book. It has survived not only five centuries, but also the leap into electronic typesetting, remaining essentially unchanged. It was popularised in the 1960s with the release of Kernwell sheets containing Lorem Ipsum passages, and more recently with desktop publishing software like Folio Layout including versions of Lorem Ipsum.</p>
    <p class="regards">Best Regards,</p>
    <div class="signature" role="img" aria-label="Handwritten signature"></div>
    <p class="signer"><b>Peter Lang</b><br>Director</p>
    <p>ABC Building, def St., Country Name</p>
  </div>
  <div class="footer-band">www.<b>Rwbuild</b>.net</div>
</section>

<section class="sheet folder">
  <div class="brand-name">R&amp;W</div>
  <div class="services">Electrical<br>Refrigeration<br>Building Services</div>
  <div class="footer-band">www.<b>Rwbuild</b>.net</div>
</section>

<section class="sheet card-front">
  <div class="brand-name">R&amp;W</div>
  <div class="services">Electrical<br>Refrigeration<br>Building Services</div>
  <div class="contact">555.010.4471<br>office@rwbuild.net<br>27 Ochre Street Tennant Creek NT 0860</div>
  <div class="holder"><b>Dana Whitlock</b><br><span>Owner</span></div>
  <div class="footer-band">www.<b>Rwbuild</b>.net</div>
</section>

<section class="sheet card-back">
  <div class="brand-name">R&amp;W</div>
</section>

<section class="sheet envelope">
  <div class="brand-name">R&amp;W</div>
  <div class="services">Electrical<br>Refrigeration<br>Building Services</div>
  <div class="footer-band">www.<b>Rwbuild</b>.net</div>
</section>

<section class="sheet envelope-back">
  <div class="flap">www.<b>Rwbuild</b>.net</div>
</section>

</body>
</html>
```